Super Greens Label for Supplement Bottle

We want to design a front label for a health supplement bottle. The product is called Meadow Crunch Chews™. This will be a new product so there is no current website for the product. The focus is on supergreens that taste great and deliver support for energy, digestion, and immune defense.
We want it to be modern, vibrant and appealing.
Bottle size: standard size supplement CLEAR bottle size, with white child resistant cap and the label panel dimensions are 3” x 7”. The label should be primarily white and green, with a touch of red; (see color palettes)/it can also ONLY be white and green. See samples attached.
We are only focused on the front of the bottle design, not on the back, but leave space for the supplement panel and other text on the back.
So the text for the front of the bottle is:
RT Halvorsen's
Meadow Crunch Chews™
Super Greens Blend for:
Energy, Digestion, and Immune Support*
60 Gummies | Dietary Supplement
Raspberry Flavor Gummies
Off to side of the label:
Non-GMO
Vegan Friendly
Plant-Based
Gelatin Free
Colors
Designer to choose colors to be used in the design.
Look and feel
Each slider illustrates characteristics of the customer's brand and the style your logo design should communicate.

```html
<!DOCTYPE html>
<html lang="en">
<head>
<meta charset="utf-8">
<title>Meadow Crunch Chews – Front Label</title>
<link href="https://fonts.googleapis.com/css2?family=Inter:wght@400;500;600&family=Great+Vibes&display=swap" rel="stylesheet">
<style>
  :root {
    --backdrop: #00bfb3;
    --green-deep: #013d10;
    --green-mid: #02561a;
    --green-bright: #066b16;
    --white: #ffffff;
    --pill-text: #045f17;
    --soft-white: #eef3ee;
  }
  * { margin: 0; padding: 0; box-sizing: border-box; }
  html, body { width: 1200px; height: 900px; overflow: hidden; }
  body {
    background: var(--backdrop);
    font-family: "Inter", Arial, sans-serif;
    position: relative;
  }
  .label {
    position: absolute;
    left: 220px; top: 190px;
    width: 760px; height: 520px;
    background: linear-gradient(100deg, var(--green-deep) 0%, var(--green-mid) 55%, var(--green-bright) 100%);
    border-radius: 6px;
    color: var(--white);
  }
  .claims-strip {
    position: absolute;
    left: 0; top: 0;
    width: 44px; height: 345px;
    background: var(--soft-white);
    border-radius: 0 0 22px 0;
    display: flex; flex-direction: column;
    align-items: center; justify-content: space-around;
    padding: 30px 0 20px;
  }
  .claim-badge { width: 20px; height: 20px; border: 1.5px solid var(--green-mid); border-radius: 50%; }
  .brand-block {
    position: absolute;
    left: 44px; right: 0; top: 36px;
    display: flex; flex-direction: column; align-items: center;
  }
  .maker {
    font-size: 30px; font-weight: 500; letter-spacing: 3px;
    display: flex; align-items: center; gap: 10px;
    margin-left: 60px;
  }
  .maker-dot { width: 16px; height: 16px; border-radius: 50%; background: var(--white); }
  .product-name {
    font-size: 108px; font-weight: 500; line-height: 0.9;
    letter-spacing: -3px; text-align: center;
    margin-top: 14px; margin-left: 60px;
  }
  .product-type {
    display: flex; align-items: center; gap: 14px;
    margin-top: 16px; margin-left: 60px;
    font-size: 17px; font-weight: 600; letter-spacing: 5px;
  }
  .product-type::before, .product-type::after {
    content: ""; width: 120px; height: 2px; background: var(--white);
  }
  .flavor-line {
    font-family: "Great Vibes", cursive;
    font-size: 32px; margin-top: 22px; margin-left: 60px;
  }
  .benefits {
    display: flex; gap: 6px; margin-top: 12px; margin-left: 30px;
  }
  .benefit {
    background: var(--white); color: var(--pill-text);
    font-size: 28px; font-weight: 500; letter-spacing: -0.5px;
    padding: 12px 12px;
  }
  .benefit:first-child { border-radius: 10px 0 0 10px; }
  .benefit:last-child { border-radius: 0 10px 10px 0; }
  .supplement-line {
    margin-top: 30px; margin-left: 60px;
    font-size: 20px; font-weight: 400; letter-spacing: 0.3px;
  }
  .supplement-line strong { font-weight: 600; }
</style>
</head>
<body>
  <section class="label">
    <aside class="claims-strip" aria-label="Non-GMO, Vegan Friendly, Plant-Based, Gelatin Free">
      <span class="claim-badge"></span>
      <span class="claim-badge"></span>
      <span class="claim-badge"></span>
      <span class="claim-badge"></span>
    </aside>
    <div class="brand-block">
      <div class="maker"><span>RT HALVORSEN’S</span><span class="maker-dot"></span></div>
      <h1 class="product-name">MEADOW<br>CRUNCH</h1>
      <div class="product-type">CHEWS™</div>
      <p class="flavor-line">Raspberry Flavor Gummies Blend for:</p>
      <div class="benefits">
        <span class="benefit">Energy</span>
        <span class="benefit">Digestion</span>
        <span class="benefit">Immune Support</span>
      </div>
      <p class="supplement-line">DIETARY SUPPLEMENT | <strong>60 GUMMIES</strong></p>
    </div>
  </section>
</body>
</html>
```